Business Card Design of an established Waste Management, Plastic Recycling and Renewable Energy Comp

We are looking for business card design for plastic card with holograms (Very similar to credit card). I will provide our logo (Quenbys). So the name on the business card will be our logo )Quenbys) + Environmental next to it, so it will read Quenbys Environmental. The font for Environmental does not to be the same as the font of the logo. The holograms will be used to display ISO14001 Certified (In normal credit card, normally on the holograms, they show nova or kelo). I will post the design requirements from the card printing company very shortly to make sure they can use the design for the plastic card.

Target Market(s)

Companies, Government Organizations, Corporations.

Industry/Entity Type

Business

Contact Information for Business Card

Motto (Under the logo): Cleaner By Design
Name: Leopold Maresca; Position: Business Manager; Address: Pelmore Landfill & Recycling Facility, Tressingham Rd, Halvern Downs, WA 6122; Ph: +61 8 5210 4738; Mob: +61 455 903 172; E: Leo@quenbysenvironmental-mail.com

Requirements
Must have
• Business Names: Quenbys Logo + Environmental word after the logo.
• Motto (Under the logo): Cleaner By Design
• All the Business Card Details above.
• Hologram Logo on the lower right corner which says: ISO 14001 Certified.
• Please remember the design will be printed on plastic card Not paper. The plastic crad is the same as credit card. Hope this helps. Thank You

```html
<!DOCTYPE html>
<html lang="en">
<head>
<meta charset="utf-8">
<title>Quenbys Environmental – Business Card</title>
<link href="https://fonts.googleapis.com/css2?family=Open+Sans:wght@400;600;700&display=swap" rel="stylesheet">
<style>
  :root {
    --bg-top: #2a2a2a;
    --bg-bottom: #050505;
    --sky-blue: #2a98d8;
    --deep-blue: #045a9a;
    --white: #ffffff;
    --ink-grey: #4f5154;
    --motto-blue: #2a98d8;
    --leaf-green: #1f7a2c;
    --email-green: #1d6b22;
  }
  * { box-sizing: border-box; margin: 0; padding: 0; }
  html, body { width: 1200px; height: 900px; overflow: hidden; }
  body {
    background: linear-gradient(180deg, var(--bg-top) 0%, #161616 50%, var(--bg-bottom) 100%);
    font-family: "Open Sans", Arial, sans-serif;
    position: relative;
  }
  .card {
    position: absolute;
    width: 440px;
    height: 271px;
    border-radius: 10px;
    overflow: hidden;
    top: 306px;
  }
  /* Front card */
  .card-front { left: 148px; background: var(--sky-blue); }
  .front-disc {
    position: absolute;
    left: 178px;
    top: -36px;
    width: 300px;
    height: 300px;
    border-radius: 50%;
    background: var(--deep-blue);
    border: 3px solid var(--white);
  }
  .brand-vertical {
    position: absolute;
    left: 52px;
    top: 18px;
    height: 232px;
    writing-mode: vertical-rl;
    transform: rotate(180deg);
    color: var(--white);
    font-weight: 600;
    white-space: nowrap;
  }
  .brand-vertical .brand-name { font-size: 52px; line-height: 52px; }
  .brand-vertical .brand-sub { font-size: 15px; line-height: 18px; letter-spacing: 1px; }
  .brand-vertical .brand-motto {
    font-size: 10px; line-height: 16px; letter-spacing: 4px;
    font-weight: 400; opacity: .85;
  }
  .contact {
    position: absolute;
    left: 248px;
    color: var(--white);
  }
  .contact-name { top: 44px; font-size: 16px; font-weight: 700; }
  .contact-role { top: 70px; font-size: 12px; }
  .contact-address { top: 113px; font-size: 12px; line-height: 16px; }
  .contact-phones { top: 196px; font-size: 12px; line-height: 16px; list-style: none; }
  .contact-phones li { display: flex; align-items: center; gap: 8px; }
  .contact-phones svg { width: 10px; height: 10px; fill: var(--white); }

  /* Back card */
  .card-back { left: 608px; background: var(--white); }
  .back-brand {
    position: absolute;
    left: 0;
    right: 0;
    top: 36px;
    display: flex;
    justify-content: center;
    align-items: center;
    gap: 10px;
  }
  .back-brand-mark {
    width: 56px; height: 56px; border-radius: 50%;
    background: var(--sky-blue);
    flex: none;
  }
  .back-brand-name {
    font-size: 22px; font-weight: 700; color: var(--ink-grey);
    line-height: 1; white-space: nowrap;
  }
  .back-motto {
    position: absolute;
    left: 168px;
    top: 95px;
    font-size: 9px;
    letter-spacing: 4px;
    color: var(--motto-blue);
    white-space: nowrap;
  }
  .cert-badge {
    position: absolute;
    left: 22px;
    top: 202px;
    width: 58px;
    height: 58px;
    border-radius: 50%;
    background: radial-gradient(circle at 40% 40%, #5cb545, var(--leaf-green));
  }
  .back-email {
    position: absolute;
    left: 134px;
    top: 228px;
    font-size: 13px;
    color: var(--email-green);
    white-space: nowrap;
  }
</style>
</head>
<body>
  <section class="card card-front">
    <div class="front-disc"></div>
    <div class="brand-vertical">
      <div class="brand-name">Quenbys</div>
      <div class="brand-sub">ENVIRONMENTAL</div>
      <div class="brand-motto">CLEANER BY DESIGN</div>
    </div>
    <div class="contact contact-name">Leopold Maresca</div>
    <div class="contact contact-role">Business Manager</div>
    <div class="contact contact-address">Pelmore Landfill &amp; Recy-<br>cling Facility,<br>Tressingham Rd, Halvern</div>
    <ul class="contact contact-phones">
      <li><svg viewBox="0 0 10 10"><path d="M1 3c0-1.5 1.5-2 4-2s4 .5 4 2v1H7V3H3v1H1z M2 5h6l1 4H1z"/></svg>+61 8 5210 4738</li>
      <li><svg viewBox="0 0 10 10"><path d="M3 0h4a1 1 0 0 1 1 1v8a1 1 0 0 1-1 1H3a1 1 0 0 1-1-1V1a1 1 0 0 1 1-1zm0 1.5v6h4v-6z"/></svg>+61 455 903 172</li>
    </ul>
  </section>

  <section class="card card-back">
    <div class="back-brand">
      <div class="back-brand-mark"></div>
      <div class="back-brand-name">Quenbys Environmental</div>
    </div>
    <div class="back-motto">CLEANER BY DESIGN</div>
    <div class="cert-badge" role="img" aria-label="Certification hologram badge"></div>
    <div class="back-email">Leo@quenbysenvironmental-mail.com</div>
  </section>
</body>
</html>
```